Business Card Design

New business card design

Target Market(s)

Residential & Commercial Property Managers

Industry/Entity Type

Plumbing Services

Contact Information for Business Card

Name - Rowan Keddle, title - Director, Phone Number - 0431 286 517, email - rowan@tbk-plumbing.com.au, Company ABN - 73 215 904 386,

Font styles to use
Sans Serif

Colors
0054AA
0677BA
7BADD7
CADEEF
E8F1F8

```html
<!DOCTYPE html>
<html lang="en">
<head>
<meta charset="utf-8">
<title>TBK Plumbing – Business Card</title>
<link href="https://fonts.googleapis.com/css2?family=Montserrat:wght@500;700&display=swap" rel="stylesheet">
<style>
  :root {
    --stage: #1d1d1e;
    --card-white: #ffffff;
    --card-blue: #2aa8e0;
    --ink: #1f2530;
    --text: #111418;
  }
  * { margin: 0; padding: 0; box-sizing: border-box; }
  html, body {
    width: 1200px; height: 1059px; overflow: hidden;
    background: var(--stage);
    font-family: "Montserrat", sans-serif;
  }
  .card {
    position: absolute;
    border-radius: 23px;
    overflow: hidden;
  }
  .card--front { left: 256px; top: 89px; width: 688px; height: 391px; background: var(--card-white); }
  .card--back  { left: 253px; top: 546px; width: 695px; height: 395px; background: var(--card-blue); }

  .brand {
    position: absolute; left: 0; right: 0;
    text-align: center;
    font-family: "Montserrat", sans-serif;
    font-weight: 700;
    font-size: 56px;
    line-height: 1;
    letter-spacing: 0.04em;
    color: var(--ink);
  }
  .card--front .brand { top: 108px; }
  .card--back .brand { top: 178px; }

  .person {
    position: absolute; right: 364px; top: 246px; text-align: right;
  }
  .person__name { font-weight: 700; font-size: 23px; color: var(--ink); line-height: 1.1; }
  .person__role { font-weight: 500; font-size: 14px; color: var(--text); margin-top: 4px; }
  .divider { position: absolute; left: 342px; top: 242px; width: 2px; height: 67px; background: var(--ink); }

  .contacts { position: absolute; left: 359px; top: 236px; list-style: none; }
  .contacts li {
    display: flex; align-items: center; gap: 10px;
    height: 27px; font-size: 14px; font-weight: 500; color: var(--text);
  }
  .contacts svg { width: 15px; height: 15px; fill: var(--ink); flex: none; }

  .abn {
    position: absolute; left: 0; right: 0; top: 344px; text-align: center;
    font-size: 17px; font-weight: 500; color: var(--text);
  }
  .abn strong { font-weight: 700; }
</style>
</head>
<body>
  <section class="card card--front">
    <p class="brand">TBK Plumbing</p>

    <div class="person">
      <p class="person__name">Rowan Keddle</p>
      <p class="person__role">Director</p>
    </div>
    <span class="divider"></span>
    <ul class="contacts">
      <li>
        <svg viewBox="0 0 24 24" aria-hidden="true"><path d="M6.6 10.8a15.1 15.1 0 0 0 6.6 6.6l2.2-2.2a1 1 0 0 1 1-.25 11.4 11.4 0 0 0 3.6.57 1 1 0 0 1 1 1V20a1 1 0 0 1-1 1A17 17 0 0 1 3 4a1 1 0 0 1 1-1h3.5a1 1 0 0 1 1 1c0 1.25.2 2.45.57 3.57a1 1 0 0 1-.25 1z"/></svg>
        0431 286 517
      </li>
      <li>
        <svg viewBox="0 0 24 24" aria-hidden="true"><path d="M2 5h20v2l-10 6L2 7zm0 4.3 10 6 10-6V19H2z"/></svg>
        rowan@tbk-plumbing.com.au
      </li>
      <li>
        <svg viewBox="0 0 24 24" aria-hidden="true"><path d="M12 2a10 10 0 1 0 0 20 10 10 0 0 0 0-20zm-1 17.9A8 8 0 0 1 4.1 10.2L9 15v1a2 2 0 0 0 2 2zm6.9-2.5A2 2 0 0 0 16 16h-1v-3a1 1 0 0 0-1-1H8v-2h2a1 1 0 0 0 1-1V7h2a2 2 0 0 0 2-2v-.4a8 8 0 0 1 2.9 12.8z"/></svg>
        www.tbk-plumbing.com.au
      </li>
    </ul>

    <p class="abn"><strong>ABN</strong> - 73 215 904 386</p>
  </section>

  <section class="card card--back">
    <p class="brand">TBK Plumbing</p>
  </section>
</body>
</html>
```